professional business card design for technology company

We are a small technology consulting firm, specialising in consulting based around Cloud and Managed services. Our colour scheme is yellow, blue and white, as you can see in the logos. Although we are based in melbourne australia, due to the nature of our work, our clients can be located anywhere. We are looking for a clean, professional, positive look - similar to our company logo

Target Market(s)

small business

Industry/Entity Type

Business

Contact Information for Business Card

eye catching, designed to incorporate some level of raised printing. Must contain website address, phone number, name and job title

Requirements
Must have
• Logo (attached) - use of the same colour scheme

```html
<!DOCTYPE html>
<html lang="en">
<head>
<meta charset="utf-8">
<title>Norvale Business Card</title>
<link href="https://fonts.googleapis.com/css2?family=Raleway:wght@400;500;800&display=swap" rel="stylesheet">
<style>
  :root {
    --bg: #e6e3df;
    --card: #1a1a1a;
    --yellow: #f5d000;
    --blue: #2aa6dc;
    --grey: #5b5b5b;
    --white: #ffffff;
    --muted: #9a9a9a;
  }
  * { margin: 0; padding: 0; box-sizing: border-box; }
  html, body { width: 1200px; height: 960px; overflow: hidden; }
  body {
    background: var(--bg);
    font-family: "Raleway", sans-serif;
    display: flex;
    flex-direction: column;
    align-items: center;
    justify-content: center;
    gap: 60px;
  }
  .card {
    position: relative;
    width: 700px;
    height: 400px;
    background: var(--card);
    overflow: hidden;
    box-shadow: 0 6px 18px rgba(0,0,0,0.18);
  }

  /* Front */
  .front .accent {
    position: absolute;
    background: var(--yellow);
  }
  .front .accent-left {
    left: 0; top: 150px; width: 92px; height: 105px;
    border-right: 6px solid var(--blue);
  }
  .front .accent-right {
    right: 0; top: 40px; width: 82px; height: 95px;
    border-left: 6px solid var(--blue);
  }
  .brand {
    display: flex;
    align-items: center;
    gap: 22px;
  }
  .front .brand {
    position: absolute;
    left: 150px; top: 150px;
  }
  .brand-dot {
    width: 64px; height: 64px;
    border-radius: 50%;
    background: var(--blue);
  }
  .brand-name {
    font-weight: 800;
    font-size: 84px;
    line-height: 1;
    letter-spacing: -2px;
    color: var(--grey);
  }

  /* Back */
  .back .rule {
    position: absolute;
    left: 0; right: 0; height: 6px;
    background: var(--yellow);
  }
  .back .rule-top { top: 0; }
  .back .rule-bottom { bottom: 0; }
  .back .brand {
    position: absolute;
    left: 56px; top: 110px;
    flex-direction: column;
    align-items: center;
    gap: 18px;
  }
  .back .brand-dot { width: 110px; height: 110px; }
  .back .brand-name { font-size: 78px; }

  .contact {
    position: absolute;
    left: 400px; top: 104px;
    list-style: none;
  }
  .contact li {
    display: flex;
    align-items: center;
    gap: 14px;
  }
  .contact .person { margin-bottom: 48px; }
  .contact .line + .line { margin-top: 12px; }
  .icon {
    flex: none;
    width: 32px; height: 32px;
    border: 2px solid var(--yellow);
    border-radius: 50%;
    display: flex;
    align-items: center;
    justify-content: center;
  }
  .person .icon { width: 42px; height: 42px; }
  .icon svg { fill: var(--white); }
  .holder-name {
    font-weight: 500;
    font-size: 22px;
    letter-spacing: 0.5px;
    color: var(--grey);
    text-transform: uppercase;
  }
  .holder-name .surname { color: var(--yellow); }
  .holder-role {
    font-size: 14px;
    color: var(--muted);
  }
  .detail {
    font-size: 15px;
    color: var(--white);
  }
</style>
</head>
<body>

  <section class="card front" aria-label="Card front">
    <div class="accent accent-left"></div>
    <div class="accent accent-right"></div>
    <div class="brand">
      <span class="brand-dot"></span>
      <span class="brand-name">Norvale</span>
    </div>
  </section>

  <section class="card back" aria-label="Card back">
    <div class="rule rule-top"></div>
    <div class="rule rule-bottom"></div>

    <div class="brand">
      <span class="brand-dot"></span>
      <span class="brand-name">Norvale</span>
    </div>

    <ul class="contact">
      <li class="person">
        <span class="icon">
          <svg width="20" height="20" viewBox="0 0 20 20" aria-hidden="true">
            <circle cx="10" cy="6" r="4"/>
            <path d="M2 18c0-4.4 3.6-7 8-7s8 2.6 8 7z"/>
          </svg>
        </span>
        <div>
          <div class="holder-name">Daniel <span class="surname">Mercer</span></div>
          <div class="holder-role">Sales Director</div>
        </div>
      </li>
      <li class="line">
        <span class="icon">
          <svg width="16" height="16" viewBox="0 0 16 16" aria-hidden="true">
            <path d="M1 3h14v10H1z M1 3l7 5 7-5" fill="none" stroke="#fff" stroke-width="1.6"/>
          </svg>
        </span>
        <span class="detail">hello@norvale.com</span>
      </li>
      <li class="line">
        <span class="icon">
          <svg width="16" height="16" viewBox="0 0 16 16" aria-hidden="true">
            <g fill="none" stroke="#fff" stroke-width="1.4">
              <circle cx="8" cy="8" r="6.5"/>
              <ellipse cx="8" cy="8" rx="3" ry="6.5"/>
              <path d="M1.5 8h13"/>
            </g>
          </svg>
        </span>
        <span class="detail">www.norvale.com</span>
      </li>
      <li class="line">
        <span class="icon">
          <svg width="16" height="16" viewBox="0 0 16 16" aria-hidden="true">
            <path d="M3.5 1.5l2.5 3-1.5 1.8c.8 1.8 2.4 3.4 4.2 4.2l1.8-1.5 3 2.5-1.2 2.5C7.5 14 2 8.5 1 2.7z"/>
          </svg>
        </span>
        <span class="detail">555-018-2741</span>
      </li>
    </ul>
  </section>

</body>
</html>
```